Transform Your Giving

I need a tri-fold brochure that will fit in a standard number 10 business envelope. Meadowlark and Allied Services is a charitable nonprofit. The goal of this brochure is to stimulate people into thinking about other ways to make a donation. The design should communicate the essential information on donation options, create a sense of professional integrity, be graphically sharp, easy to read and laid out in a way that doesn't make the material appear crowded.

```html
<!DOCTYPE html>
<html lang="en">
<head>
<meta charset="utf-8">
<title>Transform Your Giving – Meadowlark and Allied Services</title>
<link rel="stylesheet" href="https://fonts.googleapis.com/css2?family=Open+Sans:ital,wght@0,400;0,600;0,700;0,800;1,400;1,600&family=Montserrat:ital,wght@1,300&display=swap">
<style>
  :root{
    --green:#4bb648;
    --green-deep:#2f8f2c;
    --green-pale:#e3f2dc;
    --navy:#2f2a6b;
    --navy-ink:#2e2a6b;
    --white:#ffffff;
    --ink:#1f1d4d;
  }
  *{box-sizing:border-box;margin:0;padding:0}
  html,body{width:1200px;height:921px;overflow:hidden;background:#fff}
  body{font-family:"Open Sans",Arial,sans-serif;color:var(--ink)}
  .brochure{position:relative;width:1200px;height:921px;overflow:hidden}
  .panel{position:absolute;top:0;height:921px;width:400px;overflow:hidden}

  /* left panel */
  .panel--impact{left:0;background:var(--green)}
  .impact-photo{position:absolute;left:0;top:0;width:400px;height:430px;
    background:linear-gradient(160deg,#b9dc9a 0%,#8fc77a 35%,#d08f74 60%,#6fb25e 100%)}
  .impact-photo::after{content:"";position:absolute;left:0;right:0;bottom:0;height:80px;
    background:linear-gradient(to bottom,rgba(75,182,72,0),var(--green))}
  .impact-title{position:absolute;left:9px;top:424px;font-weight:800;font-size:28.5px;color:var(--white);
    letter-spacing:.3px;text-shadow:0 2px 0 rgba(47,143,44,.6)}
  .impact-copy{position:absolute;left:29px;width:347px;font-size:19.5px;line-height:23.3px;
    color:var(--navy-ink);font-weight:600;text-align:justify}
  .impact-copy--one{top:466px}
  .impact-copy--two{top:566px}
  .option{position:absolute;width:110px;margin-left:-55px;text-align:center}
  .option svg{display:block;margin:0 auto}
  .option-label{font-weight:700;font-size:13px;line-height:11px;color:var(--navy-ink);margin-top:6px}

  /* middle panel */
  .panel--contact{left:400px;background:var(--navy);color:var(--white)}
  .intro-bracket{position:absolute;left:16px;top:22px;width:68px;height:62px;
    border-left:1.5px solid var(--white);border-top:1.5px solid var(--white)}
  .intro{position:absolute;left:27px;top:32px;width:330px;font-size:15.3px;line-height:17.9px}
  .quote-band{position:absolute;left:0;top:166px;width:400px;height:136px;background:var(--green)}
  .quote-mark{position:absolute;font-family:Georgia,serif;font-weight:700;font-size:92px;line-height:1;color:var(--white)}
  .quote-mark--open{left:18px;top:140px}
  .quote-mark--close{left:325px;top:276px}
  .quote{position:absolute;left:20px;top:202px;width:362px;text-align:center;
    font-family:"Montserrat",Arial,sans-serif;font-style:italic;font-weight:300;font-size:23.5px;line-height:30px;color:var(--white)}
  .quote-author{position:absolute;left:0;top:278px;width:400px;text-align:center;font-size:9.5px;
    font-variant:small-caps;letter-spacing:.3px;color:var(--white)}
  .will{position:absolute;left:0;width:400px;text-align:center;font-size:16px;line-height:19px}
  .will--lead{top:344px}
  .will-link{position:absolute;left:119px;top:368px;width:163px;height:28px;border:2px solid var(--white);
    border-radius:6px;box-shadow:2px 2px 0 #1b1846;text-align:center;font-weight:700;font-size:15px;line-height:24px}
  .will--note{top:401px}
  .contact-head{position:absolute;left:18px;top:480px;font-weight:800;font-size:14.5px;letter-spacing:.3px}
  .contact-sub{position:absolute;left:18px;top:500px;width:360px;font-style:italic;font-size:12.6px;line-height:13.5px}
  .contact-row{position:absolute;left:38px;display:flex;align-items:center;gap:8px;font-size:14.5px}
  .contact-row svg{flex:none}
  .org-name{position:absolute;left:0;top:700px;width:400px;text-align:center;font-weight:800;font-size:24px;
    line-height:28px;color:var(--white)}
  .follow{position:absolute;left:67px;top:816px;display:flex;align-items:center;gap:9px;font-size:8px;font-weight:600}
  .follow-dot{width:17px;height:17px;border-radius:50%;background:var(--white)}
  .rule{position:absolute;left:17px;top:839px;width:366px;height:1px;background:var(--green)}
  .disclaimer{position:absolute;left:17px;top:847px;width:366px;font-style:italic;font-size:9.4px;line-height:12px;
    text-align:justify;letter-spacing:.2px}

  /* right panel */
  .panel--cover{left:800px;
    background:linear-gradient(135deg,#2f9a2f 0%,#57bb3f 30%,#b7de86 55%,#6cc14e 75%,#2c7f33 100%)}
  .cover-photo{position:absolute;inset:0;background:radial-gradient(ellipse 60% 45% at 62% 40%,rgba(230,245,205,.55),rgba(230,245,205,0) 70%)}
  .top-option{position:absolute;top:-16px;width:76px;margin-left:-38px;text-align:center}
  .top-option .disc{width:76px;height:76px;border-radius:50%;background:var(--green-pale);
    display:flex;align-items:flex-end;justify-content:center;padding-bottom:10px}
  .top-option-label{font-size:9.5px;line-height:7.5px;color:var(--white);margin-top:2px;font-weight:600}
  .tag{position:absolute;top:532px;height:33px;border:1.5px dashed var(--white);border-radius:17px;padding:2px}
  .tag span{display:block;height:100%;background:var(--white);border-radius:14px;color:var(--green);
    font-weight:600;font-size:17.5px;line-height:25px;padding:0 9px}
  .headline{position:absolute;right:18px;text-align:right;font-weight:800;color:var(--white);letter-spacing:-1px;
    text-shadow:3px 3px 0 var(--green-deep)}
  .headline--transform{top:568px;font-size:73px;line-height:80px}
  .headline--your{top:625px;font-size:112px;line-height:118px}
  .headline--giving{top:717px;font-size:108px;line-height:116px}
  .cover-tab{position:absolute;left:28px;top:845px;width:400px;height:90px;background:var(--white);border-radius:38px 0 0 38px}
  .cover-tab-copy{position:absolute;left:52px;top:858px;font-style:italic;font-weight:600;font-size:18.5px;line-height:18px;color:var(--ink)}
  .cover-tab-name{position:absolute;left:258px;top:862px;width:140px;font-weight:800;font-size:15px;line-height:17px;color:var(--navy-ink)}
</style>
</head>
<body>
<main class="brochure">

  <section class="panel panel--impact">
    <div class="impact-photo" role="img" aria-label="Photograph of a young woman and her mother embracing outdoors, holding red tulips"></div>
    <h2 class="impact-title">THE IMPACT OF YOUR GIFT</h2>
    <p class="impact-copy impact-copy--one">Your generosity drives our mission. With every Smart gift you’re supporting Meadowlark and Allied Services.</p>
    <p class="impact-copy impact-copy--two">Join our community of Smart Givers today and make an enduring impact. With Smart Giving your generosity reaches further. Begin your Smart Giving journey with us today.</p>

    <div class="option" style="left:94px;top:705px">
      <svg width="66" height="66" viewBox="0 0 66 66"><circle cx="33" cy="33" r="31" fill="var(--green-pale)" stroke="var(--navy)" stroke-width="4"/><circle cx="33" cy="33" r="16" fill="var(--navy)"/><path d="M38 27a8 8 0 1 0 1 9" fill="none" stroke="#fff" stroke-width="2.5"/><path d="M36 23l3 4-4 2" fill="none" stroke="#fff" stroke-width="2"/></svg>
      <div class="option-label">CRYPTO</div>
    </div>
    <div class="option" style="left:199px;top:705px">
      <svg width="66" height="66" viewBox="0 0 66 66"><circle cx="33" cy="33" r="31" fill="var(--green-pale)" stroke="var(--navy)" stroke-width="4"/><path d="M19 28l14-8 14 8z" fill="none" stroke="var(--navy)" stroke-width="2"/><g fill="none" stroke="var(--navy)" stroke-width="2"><rect x="22" y="31" width="4" height="10"/><rect x="31" y="31" width="4" height="10"/><rect x="40" y="31" width="4" height="10"/><path d="M19 44h28"/></g></svg>
      <div class="option-label">DAF’s</div>
    </div>
    <div class="option" style="left:303px;top:705px">
      <svg width="66" height="66" viewBox="0 0 66 66"><circle cx="33" cy="33" r="31" fill="var(--green-pale)" stroke="var(--navy)" stroke-width="4"/><g fill="var(--navy)"><rect x="19" y="36" width="6" height="9"/><rect x="28" y="31" width="6" height="14"/><rect x="37" y="25" width="6" height="20"/></g><path d="M18 32l10-6 6 3 9-8" fill="none" stroke="var(--navy)" stroke-width="2"/></svg>
      <div class="option-label">STOCKS<br>&amp; SECURITIES</div>
    </div>
    <div class="option" style="left:144px;top:809px">
      <svg width="66" height="66" viewBox="0 0 66 66"><circle cx="33" cy="33" r="31" fill="var(--green-pale)" stroke="var(--navy)" stroke-width="4"/><rect x="20" y="29" width="26" height="17" fill="var(--navy)"/><rect x="19" y="25" width="28" height="5" fill="var(--navy)"/><path d="M33 25c-4-6-9-4-6-1m6 1c4-6 9-4 6-1" fill="none" stroke="var(--navy)" stroke-width="2"/></svg>
      <div class="option-label">QCDs</div>
    </div>
    <div class="option" style="left:251px;top:809px">
      <svg width="66" height="66" viewBox="0 0 66 66"><circle cx="33" cy="33" r="31" fill="var(--green-pale)" stroke="var(--navy)" stroke-width="4"/><rect x="18" y="24" width="30" height="21" rx="3" fill="none" stroke="var(--navy)" stroke-width="2.5"/><path d="M18 32h30" stroke="var(--navy)" stroke-width="2"/><circle cx="33" cy="30" r="5" fill="var(--navy)"/></svg>
      <div class="option-label">CHARITABLE<br>ANNUITY</div>
    </div>
  </section>

  <section class="panel panel--contact">
    <div class="intro-bracket"></div>
    <p class="intro">To learn more about Smart Giving Options and how they can benefit you and Meadowlark and Allied Services, please reach out to our team. We’re here to help you navigate these giving methods and answer any question you may have.</p>
    <div class="quote-band"></div>
    <span class="quote-mark quote-mark--open">“</span>
    <p class="quote">Being kind to others is a way of being good to yourself.</p>
    <p class="quote-author">~Miriam Castellane~</p>
    <span class="quote-mark quote-mark--close">”</span>

    <p class="will will--lead">If you do not have a will, go to:</p>
    <div class="will-link">www.WillStarter.org</div>
    <p class="will will--note">In 20 minutes you can have a<br>legal will – for free.</p>

    <h3 class="contact-head">CONTACT US</h3>
    <p class="contact-sub">Have more question? Please contact us at Meadowlark and Allied Services:</p>
    <div class="contact-row" style="top:533px">
      <svg width="16" height="18" viewBox="0 0 16 18"><path d="M8 17s6-6 6-10A6 6 0 0 0 2 7c0 4 6 10 6 10z" fill="none" stroke="#fff" stroke-width="1.3"/><circle cx="8" cy="7" r="2.2" fill="none" stroke="#fff" stroke-width="1.3"/></svg>
      <span>1420 Prairie View Rd. Suite 4 Fargo, ND 58102</span>
    </div>
    <div class="contact-row" style="top:564px">
      <svg width="16" height="16" viewBox="0 0 16 16"><path d="M4 1l3 3-2 2c1 2 3 4 5 5l2-2 3 3-2 3C7 15 1 9 1 3z" fill="none" stroke="#fff" stroke-width="1.2"/></svg>
      <span>701-555-0148 (ext. 100)</span>
    </div>
    <div class="contact-row" style="top:588px">
      <svg width="18" height="14" viewBox="0 0 18 14"><rect x="1" y="1" width="16" height="12" fill="none" stroke="#fff" stroke-width="1.2"/><path d="M1 1l8 7 8-7" fill="none" stroke="#fff" stroke-width="1.2"/></svg>
      <span>lhartwell@meadowlarkallied.org</span>
    </div>
    <div class="contact-row" style="top:612px">
      <svg width="16" height="16" viewBox="0 0 16 16"><circle cx="8" cy="8" r="7" fill="none" stroke="#fff" stroke-width="1.2"/><ellipse cx="8" cy="8" rx="3" ry="7" fill="none" stroke="#fff" stroke-width="1.2"/><path d="M1 8h14M2 4.5h12M2 11.5h12" stroke="#fff" stroke-width="1"/></svg>
      <span>www.meadowlarkallied.org</span>
      <svg width="12" height="14" viewBox="0 0 12 14"><path d="M1 1l10 6-4 1 3 5-2 1-3-5-3 3z" fill="#fff"/></svg>
    </div>

    <p class="org-name">Meadowlark and Allied<br>Services, Inc.</p>

    <div class="follow">
      <span>FOLLOW US</span>
      <span class="follow-dot"></span><span class="follow-dot"></span><span class="follow-dot"></span>
      <span class="follow-dot"></span><span class="follow-dot"></span><span class="follow-dot"></span>
    </div>
    <div class="rule"></div>
    <p class="disclaimer">This material has been prepared for informational purposes only and is not intended to provide tax, accounting, or legal advice. Meadowlark and Allied Services is not a professional fiduciary organization. Please consult with your tax advisor or financial professional before making a decision about Smart Giving.</p>
  </section>

  <section class="panel panel--cover">
    <div class="cover-photo" role="img" aria-label="Photograph of a smiling bearded man, tinted green"></div>

    <div class="top-option" style="left:37px"><div class="disc"><svg width="26" height="26" viewBox="0 0 26 26"><circle cx="13" cy="13" r="12" fill="var(--green)"/><path d="M17 9a6 6 0 1 0 1 7" fill="none" stroke="#fff" stroke-width="2"/></svg></div><div class="top-option-label">CRYPTO</div></div>
    <div class="top-option" style="left:118px"><div class="disc"><svg width="26" height="24" viewBox="0 0 26 24"><path d="M2 8l11-6 11 6z" fill="none" stroke="var(--green)" stroke-width="2"/><path d="M5 11v8M11 11v8M17 11v8M22 11v8M2 22h22" stroke="var(--green)" stroke-width="2"/></svg></div><div class="top-option-label">DAF’s</div></div>
    <div class="top-option" style="left:199px"><div class="disc"><svg width="26" height="24" viewBox="0 0 26 24"><g fill="var(--green)"><rect x="3" y="14" width="5" height="8"/><rect x="10" y="10" width="5" height="12"/><rect x="17" y="5" width="5" height="17"/></g></svg></div><div class="top-option-label">STOCKS<br>&amp; SECURITIES</div></div>
    <div class="top-option" style="left:280px"><div class="disc"><svg width="24" height="24" viewBox="0 0 24 24"><rect x="3" y="9" width="18" height="13" fill="none" stroke="var(--green)" stroke-width="2"/><rect x="2" y="6" width="20" height="4" fill="var(--green)"/></svg></div><div class="top-option-label">QCDs</div></div>
    <div class="top-option" style="left:362px"><div class="disc"><svg width="26" height="22" viewBox="0 0 26 22"><rect x="2" y="3" width="22" height="17" rx="2" fill="none" stroke="var(--green)" stroke-width="2"/><circle cx="13" cy="9" r="4" fill="var(--green)"/></svg></div><div class="top-option-label">CHARITABLE<br>ANNUITY</div></div>

    <div class="tag" style="left:80px"><span>be strategic</span></div>
    <div class="tag" style="left:264px"><span>be smart</span></div>

    <div class="headline headline--transform">Transform</div>
    <div class="headline headline--your">Your</div>
    <div class="headline headline--giving">Giving</div>

    <div class="cover-tab"></div>
    <p class="cover-tab-copy">Discover the impact<br>of Smart Giving with</p>
    <p class="cover-tab-name">Meadowlark and Allied</p>
  </section>

</main>
</body>
</html>
```